Public Relations Agency Seeks Wordpress Design and Coding

TRELVOX Studio is a public relations agency specializing in media relations, public affairs and marketing communication.

The site should display the following visual characteristics: professionalism, trustworthiness, high-tech focus, clear and concise design.

The desired colors are royal blue, gray and hints of red.

Design look/feel inspired by this site: http://brightpathgatherings.example/

Specifications:

1. Navigation/Pages/Index:

HOME

ABOUT US

SERVICES

NEWS

CONTACT

---

2. Functionality of/content for each page:

- Home
o Dominant photo (professional, edgy, innovative)
o Simple, straightforward access to/from “Home” from other pages
o Includes logo (attached) and tagline "Unleash the power of communication"
o Direct link to “CONTACT”
o Links to social media accounts: Facebook, Twitter, LinkedIn

- About Us

o Company profile blurb
o President’s photo with short bio

- Services
o Public Relations
 Strategic communication
 Brand and reputation management
 Community relations
o Media Relations
 News coverage and contacts
 Media training and interview skills
 Crisis communications
o Congressional Affairs
 Public affairs
 Public policy
 Legislative strategy
o Mass Communication
 Speechwriting
 Presentation creation
 Social media
o Marketing Communications
 Business collateral material
 Promotional campaigns
 Special events and tradeshows

- News
o Blog-like page to post information and/or share news from other sites

- Contact
o Standard “Contact Us” form (Name, Email, Phone, Message)
o Direct Contact
 (407) 555-0164
 Marisol@TRELVOXstudio.example

Target Market(s)

Small to large businesses specializing in high technology, defense/military, medicine/healthcare, and wide array of professional services.

Industry/Entity Type

Marketing

Font styles to use
Serif
Sans Serif

Colors
0555a3
ec2027
edf3f7

Requirements
Must have
• -- Project reqires DESIGN - and - fully CODED.

-- Strong SEO

-- Optimized for mobile viewing

Thank you!

```html
<!DOCTYPE html>
<html lang="en">
<head>
<meta charset="utf-8">
<title>TRELVOX Studio – Public Relations Agency</title>
<link rel="stylesheet" href="https://fonts.googleapis.com/css2?family=Open+Sans:wght@400;600;700&family=Roboto:wght@400;500;700&display=swap">
<style>
:root{
  --blue:#0555a3;
  --royal:#1c3f92;
  --royal-deep:#122a66;
  --red:#ec2027;
  --light:#edf3f7;
  --ink:#333b45;
  --grey:#6b7480;
  --footer:#2b2e33;
  --white:#ffffff;
}
*{box-sizing:border-box;margin:0;padding:0}
html,body{width:1200px;height:2256px;overflow:hidden}
body{font-family:"Open Sans",Arial,sans-serif;color:var(--ink);background:var(--white);position:relative}
.site-header{height:72px;display:flex;align-items:center;justify-content:space-between;padding:0 56px 0 112px;background:var(--white)}
.brand{display:flex;align-items:center;gap:10px;font-family:"Roboto",sans-serif;font-weight:700;font-size:30px;color:var(--ink);letter-spacing:1px}
.brand-mark{width:14px;height:14px;background:var(--blue)}
.main-nav{display:flex}
.main-nav a{font-family:"Roboto",sans-serif;font-size:16px;color:var(--ink);text-decoration:none;padding:8px 18px}
.main-nav a.active{background:var(--blue);color:var(--white)}
.hero{position:relative;height:628px;overflow:hidden;
  background:
   radial-gradient(ellipse 260px 220px at 560px 250px,rgba(220,226,232,.55),transparent 70%),
   radial-gradient(ellipse 220px 260px at 820px 300px,rgba(200,208,216,.45),transparent 70%),
   radial-gradient(ellipse 300px 160px at 640px 470px,rgba(235,238,241,.55),transparent 70%),
   radial-gradient(ellipse 200px 300px at 250px 260px,rgba(90,100,112,.5),transparent 70%),
   linear-gradient(135deg,#1e2632 0%,#3e4956 35%,#5c6875 55%,#343e4a 80%,#161c24 100%)}
.hero-photo{position:absolute;inset:0}
.hero-tagline{position:absolute;left:350px;top:452px;width:500px;height:52px;background:rgba(20,28,38,.6);color:var(--white);font-family:"Roboto",sans-serif;font-size:26px;white-space:nowrap;display:flex;align-items:center;justify-content:center}
.slider-arrow{position:absolute;top:332px;width:40px;height:40px;border-radius:50%;background:rgba(255,255,255,.25);display:flex;align-items:center;justify-content:center}
.slider-arrow.prev{left:108px}.slider-arrow.next{right:108px}
.section-title{display:inline-block;font-family:"Roboto",sans-serif;font-weight:500;font-size:20px;padding:8px 18px;border:2px solid var(--blue);color:var(--blue);background:var(--white)}
.about{height:332px;padding:28px 124px 0}
.about-rule{border-top:2px solid var(--blue);margin-top:-22px;margin-bottom:22px}
.about .section-title{position:relative}
.about-body{display:flex;gap:40px}
.about-text{width:730px;font-size:13.5px;line-height:1.75;color:var(--grey)}
.about-text p{margin-bottom:12px}
.president-photo{width:200px;height:210px;background:
  radial-gradient(ellipse 60px 70px at 100px 80px,#e7c9b4,transparent 75%),
  linear-gradient(180deg,#cfd5dc 0%,#9aa5b1 45%,#c2343c 75%,#a82a31 100%)}
.btn{display:inline-block;font-family:"Roboto",sans-serif;font-size:12px;font-weight:700;color:var(--white);background:var(--royal);padding:8px 14px;text-decoration:none;text-transform:uppercase}
.services{height:428px;background:var(--royal);padding-top:26px;text-align:center}
.services .section-title{background:transparent;color:var(--white);border-color:var(--white)}
.service-row{display:flex;justify-content:center;gap:34px;margin-top:28px;text-align:left}
.service{width:292px;color:var(--white)}
.service h3{font-family:"Roboto",sans-serif;font-size:15px;font-weight:700;margin-bottom:10px;text-transform:uppercase}
.service-photo{height:172px;margin-bottom:10px}
.service p{font-size:12.5px;line-height:1.5;color:#d7e0f2;height:56px;margin-bottom:8px}
.service .btn{background:var(--royal-deep)}
.news{position:relative;height:360px;background:
  radial-gradient(ellipse 360px 120px at 600px 300px,rgba(150,160,175,.55),transparent 75%),
  linear-gradient(180deg,#2f3e55,#56657a 50%,#2b384d);text-align:center;padding-top:28px}
.news .section-title{background:transparent;color:var(--white);border-color:var(--white)}
.news-row{display:flex;justify-content:center;gap:36px;margin-top:26px;text-align:left}
.news-item{width:290px;color:var(--white)}
.news-item h4{font-size:13.5px;font-weight:700;line-height:1.4;margin-bottom:8px}
.news-item p{font-size:12.5px;line-height:1.55;color:#e3e8ef}
.pager{position:absolute;left:0;right:0;top:296px;display:flex;justify-content:center;gap:6px}
.pager span{width:28px;height:28px;border:1px solid var(--white);display:flex;align-items:center;justify-content:center}
.contact{height:340px;background:var(--light);padding:30px 124px 0;position:relative}
.contact-head{text-align:center}
.contact-body{display:flex;gap:60px;margin-top:30px}
.contact-info{width:330px}
.contact-info h5{font-family:"Roboto",sans-serif;font-size:13px;color:var(--blue);font-weight:700;margin-bottom:4px}
.contact-info p{font-size:12.5px;color:var(--grey);line-height:1.5;margin-bottom:14px}
.form-col{width:280px}
.form-col label,.comments label{display:block;font-size:12px;color:var(--grey);margin-bottom:4px}
.field{height:30px;background:var(--white);border:1px solid #cfd8e0;margin-bottom:14px}
.comments{width:290px}
.comments .field{height:124px}
.submit{position:absolute;right:130px;top:290px;background:var(--red);color:var(--white);font-family:"Roboto",sans-serif;font-size:12px;font-weight:700;padding:8px 16px}
.site-footer{height:96px;background:var(--footer);display:flex;justify-content:space-between;align-items:center;padding:0 124px;color:#c5cad1}
.connect h6{font-size:11px;font-weight:700;letter-spacing:1px;margin-bottom:8px}
.social{display:flex;gap:8px}
.social span{width:20px;height:20px;background:var(--blue)}
.footer-right{text-align:right;font-size:12px}
.footer-right nav a{color:#c5cad1;text-decoration:none;margin-left:10px}
.footer-right p{margin-top:6px;font-size:11px;color:#8e949c}
</style>
</head>
<body>
<header class="site-header">
  <div class="brand"><span class="brand-mark"></span>TRELVOX Studio</div>
  <nav class="main-nav">
    <a href="#" class="active">Home</a><a href="#">About us</a><a href="#">Services</a><a href="#">News</a><a href="#">Contact us</a>
  </nav>
</header>

<section class="hero">
  <div class="hero-photo" role="img" aria-label="Team of professionals gathered around a laptop in a modern office"></div>
  <div class="hero-tagline">Unleash the power of communication</div>
  <div class="slider-arrow prev"><svg width="16" height="16" viewBox="0 0 16 16"><path d="M10 2 4 8l6 6" stroke="#fff" stroke-width="2" fill="none"/></svg></div>
  <div class="slider-arrow next"><svg width="16" height="16" viewBox="0 0 16 16"><path d="M6 2l6 6-6 6" stroke="#fff" stroke-width="2" fill="none"/></svg></div>
</section>

<section class="about">
  <h2 class="section-title">ABOUT US</h2>
  <div class="about-rule"></div>
  <div class="about-body">
    <div class="about-text">
      <p>Our agency helps technology, defense and healthcare organizations tell their story with clarity and purpose. For more than fifteen years we have connected clients with reporters, policy makers and communities through careful planning, honest messaging and steady follow-through. Every campaign begins with listening, then builds a plan that fits the goals, the audience and the moment.</p>
      <p>Our president leads a small senior team with deep roots in newsrooms, government offices and corporate communication. She has guided product launches, crisis responses and public hearings, and she still reviews every major plan personally. Clients value her calm judgment, her network of trusted contacts and her belief that good work is always built on trust.</p>
      <a href="#" class="btn">Read more</a>
    </div>
    <div class="president-photo" role="img" aria-label="Portrait of the agency president"></div>
  </div>
</section>

<section class="services">
  <h2 class="section-title">SERVICES</h2>
  <div class="service-row">
    <article class="service">
      <h3>Media Relations</h3>
      <div class="service-photo" role="img" aria-label="Business hand touching a glowing network interface" style="background:radial-gradient(ellipse 90px 70px at 190px 80px,#e8eef7,transparent 75%),linear-gradient(135deg,#1f3f78,#5f82b8 55%,#b9cbe3)"></div>
      <p>News coverage, trusted press contacts, media training and clear crisis communications for every client.</p>
      <a href="#" class="btn">Read more</a>
    </article>
    <article class="service">
      <h3>Public Affairs</h3>
      <div class="service-photo" role="img" aria-label="Group of business people standing together" style="background:linear-gradient(180deg,#e9ecef 0%,#c9ced5 30%,#4b535f 55%,#2a313b 100%)"></div>
      <p>Public policy insight, legislative strategy and steady outreach to officials and the wider community.</p>
      <a href="#" class="btn">Read more</a>
    </article>
    <article class="service">
      <h3>Marketing Communication</h3>
      <div class="service-photo" role="img" aria-label="Silhouettes of a team meeting at a long table" style="background:linear-gradient(180deg,#f4f6f8 0%,#dfe3e8 40%,#3b424c 62%,#6e7680 80%,#d5d9de 100%)"></div>
      <p>Business collateral, promotional campaigns, special events and tradeshows that keep your brand visible.</p>
      <a href="#" class="btn">Read more</a>
    </article>
  </div>
</section>

<section class="news" role="img" aria-label="Background of team hands joined together">
  <h2 class="section-title">NEWS</h2>
  <div class="news-row">
    <article class="news-item">
      <h4>Agency expands its team to support new defense sector clients</h4>
      <p>Three senior advisers join the firm this spring, bringing years of experience in policy, press work and program outreach.</p>
    </article>
    <article class="news-item">
      <h4>Five habits of brands that handle a crisis with calm confidence</h4>
      <p>Preparation, a single clear voice and fast honest updates remain the strongest tools when the headlines turn difficult.</p>
    </article>
    <article class="news-item">
      <h4>Healthcare launch earns wide regional coverage in its first week</h4>
      <p>A focused media plan placed our client in print, radio and online outlets across the region within only a few days.</p>
    </article>
  </div>
  <div class="pager">
    <span><svg width="10" height="10" viewBox="0 0 10 10"><path d="M7 1 3 5l4 4" stroke="#fff" stroke-width="1.6" fill="none"/></svg></span>
    <span><svg width="10" height="10" viewBox="0 0 10 10"><path d="M3 1l4 4-4 4" stroke="#fff" stroke-width="1.6" fill="none"/></svg></span>
  </div>
</section>

<section class="contact">
  <div class="contact-head"><h2 class="section-title">CONTACT US</h2></div>
  <div class="contact-body">
    <div class="contact-info">
      <h5>ADDRESS</h5>
      <p>P.O. Box 4420, Harbor Business Park<br>Orlando, Florida</p>
      <h5>PHONE</h5>
      <p>(407) 555-0164<br>1-877-555-0190</p>
      <h5>EMAIL</h5>
      <p>Marisol@TRELVOXstudio.example<br>hello@trelvoxstudio.example</p>
    </div>
    <div class="form-col">
      <label>Name</label><div class="field"></div>
      <label>Email</label><div class="field"></div>
      <label>Phone</label><div class="field"></div>
    </div>
    <div class="comments">
      <label>Comments</label>
      <div class="field"></div>
    </div>
  </div>
  <div class="submit">SUBMIT</div>
</section>

<footer class="site-footer">
  <div class="connect">
    <h6>CONNECT WITH US</h6>
    <div class="social"><span></span><span></span><span></span></div>
  </div>
  <div class="footer-right">
    <nav><a href="#">Home</a>|<a href="#">About us</a>|<a href="#">Services</a>|<a href="#">News</a>|<a href="#">Contact us</a></nav>
    <p>Copyright © 2014 All Rights Reserved</p>
  </div>
</footer>
</body>
</html>
```